International Clinical Software Company needs a new business card design

We are looking for a new business card design for our company that has recently expanded into the UK market, making us a multinational company.
After having rebranded our website and produced a new style guide, we are looking for a business card that is creative and attention grabbing, while being consistent with the style and colour scheme used on the new website, www.plumvora.example
We produce care management technology for the aged care market, but the main aspect we aim to communicate is the human element of our software, and the way it assists in providing better care for aged people, and stronger relationships between aged people and the staff that care for them.
Our current business card is a dark green with gold text, which makes the text quite difficult to read, not very aesthetically appealing and the colour scheme looks quite dated.
We would like something fresh and modern, that can still be colourful but doesn't use large blocks of dark colour, and uses the colours within our logo.
Something tying in with the leaves that are used in our logo could work quite nicely, along with the Autumn/Fall colours of soft greens, yellows and reds (also in our existing logo). However also happy to look at fresh, completely out of the box ideas we may not have yet considered.
Target Market(s)
The people that receive this business card work in the aged card or health industry and are either corporate/management level staff or clinical (Registered Nurses, care workers etc.)
Industry/Entity Type
Health Product
Contact Information for Business Card
Company Name - BrindlewayCare
Company locations: United Kingdom, Australia, New Zealand
Staff Details:
Staff name: Derek Mallow
Staff job title: Executive Chairman
Staff email: d.mallow@plumvora.example
Office phone number: 01742 918576
Font styles to use
Other font styles liked:
- Calibri
Requirements
Must have
- Must include the BrindlewayCare brand name in it's current font
- Must include logo (3 leaves in gold circle)
- Must include Business Card Details
Nice to have
- Elements of gold
- White space
- Something autumn themed but not too cliched
Should not have
- No blue - used by a major competitor and we would like to differentiate from them
- Large blocks of dark green colour (the green that appears in our leaves on the logo on our current business card is the background colour and it is far too dark)

```html
<!DOCTYPE html>
<html lang="en">
<head>
<meta charset="utf-8">
<title>BrindlewayCare business card</title>
<link rel="stylesheet" href="https://fonts.googleapis.com/css2?family=Open+Sans:wght@300;400;600;700&display=swap">
<style>
  :root {
    --stage: #ece9e6;
    --berry: #ae1e3c;
    --white: #ffffff;
    --gold: #a8916a;
    --leaf-deep: #7a1410;
    --leaf-red: #c2301c;
    --leaf-orange: #e58a2a;
    --leaf-yellow: #ecd23a;
    --leaf-green: #8fa83a;
  }
  * { box-sizing: border-box; margin: 0; padding: 0; }
  html, body { width: 1200px; height: 900px; overflow: hidden; }
  body {
    position: relative;
    background: var(--stage);
    font-family: "Open Sans", Calibri, sans-serif;
  }
  .card {
    position: absolute;
    width: 558px;
    height: 343px;
    overflow: hidden;
    box-shadow: 0 6px 18px rgba(0,0,0,0.18);
  }
  .card-front { left: 237px; top: 61px; background: var(--berry); color: var(--white); }
  .card-back  { left: 457px; top: 518px; background: var(--white); }

  .contact { position: absolute; left: 26px; top: 44px; }
  .contact-name { font-size: 18px; font-weight: 700; line-height: 1.2; }
  .contact-title { font-size: 14px; font-weight: 400; line-height: 1.4; }
  .contact-email {
    display: flex; align-items: center; gap: 8px;
    margin-top: 15px; font-size: 14px;
  }
  .contact-email svg { width: 11px; height: 11px; fill: var(--white); }
  .contact-locations { margin-top: 15px; font-size: 14px; line-height: 1.4; }

  .brand-name {
    position: absolute;
    font-weight: 300;
    font-size: 34px;
    line-height: 1;
    white-space: nowrap;
  }
  .card-front .brand-name { right: 28px; top: 72px; color: var(--white); }

  .brand-mark {
    position: absolute; left: 110px; top: 25px;
    width: 84px; height: 84px; border-radius: 50%;
    border: 3px solid var(--gold);
  }
  .card-back .brand-name { left: 33px; top: 128px; color: var(--gold); }

  .leaf-band { position: absolute; left: 0; bottom: 0; width: 100%; }
  .card-front .leaf-band { height: 170px; }
  .card-back .leaf-band { height: 175px; }
</style>
</head>
<body>

<section class="card card-front" aria-label="Card front">
  <div class="contact">
    <p class="contact-name">Derek Mallow</p>
    <p class="contact-title">Executive Chairman</p>
    <p class="contact-email">
      <svg viewBox="0 0 24 24" aria-hidden="true"><path d="M6.6 10.8a15.1 15.1 0 0 0 6.6 6.6l2.2-2.2a1 1 0 0 1 1-.25 11.4 11.4 0 0 0 3.6.57 1 1 0 0 1 1 1V20a1 1 0 0 1-1 1A17 17 0 0 1 3 4a1 1 0 0 1 1-1h3.5a1 1 0 0 1 1 1c0 1.25.2 2.45.57 3.57a1 1 0 0 1-.25 1z"/></svg>
      d.mallow@plumvora.example
    </p>
    <p class="contact-locations">United Kingdom, Australia<br>New Zealand</p>
  </div>
  <p class="brand-name">BrindlewayCare</p>
  <svg class="leaf-band" viewBox="0 0 558 170" preserveAspectRatio="none" role="img" aria-label="Illustration of autumn leaves in deep reds along the bottom edge">
    <defs>
      <linearGradient id="front-leaves" x1="0" y1="0" x2="1" y2="1">
        <stop offset="0" stop-color="var(--leaf-red)"/>
        <stop offset="0.6" stop-color="#a3261a"/>
        <stop offset="1" stop-color="var(--leaf-deep)"/>
      </linearGradient>
    </defs>
    <path d="M0 140 C80 120 140 80 220 70 C300 50 380 20 460 10 C500 5 530 0 558 0 L558 170 L0 170 Z" fill="url(#front-leaves)"/>
  </svg>
</section>

<section class="card card-back" aria-label="Card back">
  <span class="brand-mark" aria-hidden="true"></span>
  <p class="brand-name">BrindlewayCare</p>
  <svg class="leaf-band" viewBox="0 0 560 175" preserveAspectRatio="none" role="img" aria-label="Illustration of autumn leaves in orange, yellow, green and red along the bottom edge">
    <defs>
      <linearGradient id="back-leaves" x1="0" y1="0" x2="1" y2="0">
        <stop offset="0" stop-color="var(--leaf-orange)"/>
        <stop offset="0.3" stop-color="var(--leaf-green)"/>
        <stop offset="0.55" stop-color="var(--leaf-orange)"/>
        <stop offset="0.75" stop-color="var(--leaf-red)"/>
        <stop offset="1" stop-color="var(--leaf-yellow)"/>
      </linearGradient>
    </defs>
    <path d="M0 135 C90 100 170 70 260 45 C340 25 420 10 490 0 C520 -3 545 0 560 0 L560 175 L0 175 Z" fill="url(#back-leaves)"/>
  </svg>
</section>

</body>
</html>
```